Harborview Estates Business Card for Apartment Buildings

Create business cards for resident managers who run apartment buildings. The audience is the public who are searching for apartment rentals, and current residents who live at the apartment building. Key design element will be incorporating the company logo, however, the logo cannot dominate. The building name and manager name are more important than the logo. Current business card design leaves little room for copy, so we may need to reduce the size on the current card to allow for more space for copy.

Target Market(s)

Adults 18-65 years of age, who are looking for an apartment rental, plus current residents who live at our apartment buildings.

Industry/Entity Type

Property Management

Contact Information for Business Card

A major design element will be use of the company logo. Important property and manager contact information must be part of the design. The size of the logo will need to be reduced to make room for building and manager contact copy.

Font styles to use
Sans Serif

Colors
3176b5
000000
959595
ffffff

Requirements
Must have
• 1) Incorporate the company logo.
• 2) Use the company colors (dark blue, black/grey, over white).
• 3) FEATURE THE BUILDING NAME
• 4) FEATURE THE MANAGER NAME
• 5) The company name is less important than BUILDING and MANAGER
• 6) Manager contact information
• **SEE ATTACHED CREATIVE BRIEF**
Nice to have
• 1) Back of card logo watermark
• 2) Ability to write notes on back of carfd
Should not have
• Avoid letting the company logo dominate the card, the building name and manager are more important than the company logo.

```html
<!DOCTYPE html>
<html lang="en">
<head>
<meta charset="utf-8">
<title>Harborview Estates – Resident Manager Business Card</title>
<link href="https://fonts.googleapis.com/css2?family=Roboto:wght@400;500;700&display=swap" rel="stylesheet">
<style>
  :root {
    --brand-blue: #1f63a8;
    --ink: #3a3a3a;
    --rule: #959595;
    --paper: #ffffff;
    --backdrop: #e6e6e6;
    --watermark-ring: #e8e9ec;
    --watermark-fill: #e1e5f0;
  }
  * { margin: 0; padding: 0; box-sizing: border-box; }
  html, body {
    width: 1200px; height: 960px; overflow: hidden;
    background: var(--backdrop);
    font-family: "Roboto", sans-serif;
  }
  .card {
    position: absolute;
    left: 281px;
    width: 655px; height: 374px;
    background: var(--paper);
    box-shadow: 0 2px 6px rgba(0,0,0,0.18);
  }
  .card-front { top: 80px; }
  .card-back { top: 506px; }

  .company-mark {
    position: absolute; left: 58px; top: 168px;
    display: flex; align-items: center; gap: 10px;
  }
  .company-mark .dot {
    width: 30px; height: 30px; border-radius: 50%;
    background: var(--brand-blue);
  }
  .company-mark .company-name {
    font-size: 23px; font-weight: 700; color: var(--brand-blue);
    letter-spacing: -0.2px; white-space: nowrap;
  }

  .divider {
    position: absolute; left: 328px; top: 70px;
    width: 2px; height: 236px; background: var(--rule);
  }

  .details { position: absolute; left: 361px; top: 0; right: 0; }
  .line { position: absolute; left: 0; white-space: nowrap; }
  .manager-name { top: 66px; font-size: 22px; font-weight: 700; color: var(--brand-blue); }
  .manager-title { top: 93px; font-size: 16px; color: var(--ink); }
  .building-name { top: 137px; font-size: 15px; color: var(--brand-blue); }
  .address { font-size: 15px; color: var(--ink); }
  .address.street { top: 159px; }
  .address.city { top: 181px; }

  .contact {
    position: absolute; left: 0;
    display: flex; align-items: center; gap: 9px;
    font-size: 15px; color: var(--ink); white-space: nowrap;
  }
  .contact svg { width: 15px; height: 15px; flex: none; }
  .contact.phone { top: 224px; }
  .contact.fax { top: 246px; }
  .contact.office { top: 268px; }
  .contact.email { top: 291px; }

  .watermark {
    position: absolute; left: 0; top: 0; width: 100%; height: 100%;
    display: flex; align-items: center; justify-content: center;
  }
  .watermark .ring {
    position: absolute; left: 207px; top: 65px;
    width: 240px; height: 240px; border-radius: 50%;
    border: 14px solid var(--watermark-ring);
  }
  .watermark .company-name {
    position: relative;
    font-size: 30px; font-weight: 700; color: var(--watermark-fill);
  }
</style>
</head>
<body>
  <section class="card card-front">
    <div class="company-mark">
      <span class="dot"></span>
      <span class="company-name">Harborview Estates</span>
    </div>

    <div class="divider"></div>

    <div class="details">
      <div class="line manager-name">Marisol Delgado</div>
      <div class="line manager-title">Resident Manager</div>
      <div class="line building-name">Bayside Gardens Apartments</div>
      <div class="line address street">4120 Maple Street</div>
      <div class="line address city">Port Ellis, CA 94017</div>

      <div class="contact phone">
        <svg viewBox="0 0 16 16" aria-hidden="true"><path fill="#1f63a8" d="M11 1c-3.5 1.5-6 5.5-6 9.5 0 1.8.6 3.4 1.4 4.5l2.2-1.5c-.7-.9-1.1-2-1.1-3.2 0-2.6 1.5-5.2 3.9-6.6z"/></svg>
        <span>555-204-1836</span>
      </div>
      <div class="contact fax">
        <svg viewBox="0 0 16 16" aria-hidden="true"><path fill="#1f63a8" d="M2 4h12v2H2zM3 7h10l1 7H2z"/><rect x="5" y="9" width="6" height="3" fill="#fff"/></svg>
        <span>555-387-4120</span>
      </div>
      <div class="contact office">
        <svg viewBox="0 0 16 16" aria-hidden="true"><rect x="1" y="3.5" width="14" height="9" fill="#1f63a8"/><path d="M1.5 4l6.5 5 6.5-5" fill="none" stroke="#fff" stroke-width="1.2"/></svg>
        <span>555-619-0475</span>
      </div>
      <div class="contact email">
        <svg viewBox="0 0 16 16" aria-hidden="true"><g fill="none" stroke="#1f63a8" stroke-width="1.2"><circle cx="8" cy="8" r="6.5"/><ellipse cx="8" cy="8" rx="2.8" ry="6.5"/><path d="M1.5 8h13M2.5 5h11M2.5 11h11"/></g></svg>
        <span>marisol@harborviewest.com</span>
      </div>
    </div>
  </section>

  <section class="card card-back">
    <div class="watermark">
      <span class="ring"></span>
      <span class="company-name">Harborview Estates</span>
    </div>
  </section>
</body>
</html>
```